Lmworks Business Card Design

I need a business card design for a new Business, that is focused on Custom Made Designer Furniture. that is aimed at the mid to high end markets. I would like a card that would in some way portray what I do for my clients in the way we are able to make any idea a reality and also work within a set budget to meet their requirements.
I like quite contemporary colours and styling and I want the final design to communicate a Contemporary and Professional image.

Target Market(s)

mid to high end market

Industry/Entity Type

Business

Contact Information for Business Card

Lmworks
Gareth Lindqvist
18 Wendover Ave, Auckland, New Zealand 0627.

Requirements
Nice to have
• I would also like to utilize the spot gloss or raised print on my cards

```html
<!DOCTYPE html>
<html lang="en">
<head>
<meta charset="utf-8">
<title>Lmworks Business Card</title>
<link rel="stylesheet" href="https://fonts.googleapis.com/css2?family=Roboto+Condensed:wght@300;700&display=swap">
<style>
  :root {
    --page-bg: #f2f2f2;
    --card-black: #151515;
    --brand-blue: #1ea6e6;
    --stripe-blend: #136f9f;
    --stripe-shadow: #0b3d58;
    --name-grey: #bdbdbd;
  }
  * { margin: 0; padding: 0; box-sizing: border-box; }
  html, body {
    width: 1200px;
    height: 873px;
    overflow: hidden;
    background: var(--page-bg);
  }
  .canvas {
    width: 1200px;
    height: 873px;
    display: flex;
    align-items: center;
    justify-content: center;
  }
  .business-card {
    position: relative;
    width: 740px;
    height: 484px;
    background: var(--card-black);
    overflow: hidden;
    box-shadow: 0 10px 30px rgba(0, 0, 0, 0.18);
  }
  .card-details {
    position: absolute;
    left: 56px;
    top: 58px;
    font-family: "Roboto Condensed", "Arial Narrow", sans-serif;
  }
  .company-name {
    font-weight: 700;
    font-size: 34px;
    line-height: 1;
    color: var(--brand-blue);
  }
  .person-name {
    margin-top: 4px;
    font-weight: 300;
    font-size: 50px;
    line-height: 1.05;
    color: var(--name-grey);
    white-space: nowrap;
  }
  .address {
    margin-top: 22px;
    font-weight: 700;
    font-size: 19px;
    line-height: 1.3;
    color: var(--brand-blue);
    font-style: normal;
  }
  .pattern-panel {
    position: absolute;
    top: 0;
    right: 0;
    width: 44%;
    height: 100%;
    background: linear-gradient(150deg, var(--brand-blue) 0%, var(--stripe-blend) 55%, var(--stripe-shadow) 100%);
  }
</style>
</head>
<body>
  <main class="canvas">
    <section class="business-card">
      <div class="card-details">
        <h1 class="company-name">Lmworks</h1>
        <p class="person-name">Gareth Lindqvist</p>
        <address class="address">18 Wendover Ave, Auckland<br>New Zealand 0627</address>
      </div>
      <div class="pattern-panel" role="img" aria-label="Woven pattern of bright blue diagonal stripes on black, set in interlocking hexagonal blocks like joined timber panels, suggesting crafted custom furniture"></div>
    </section>
  </main>
</body>
</html>
```